Website for a Psychologist in Private Practice

I need a cool web design for my website: www.drkalvoric.com. I would like it to look professional. Keep all the current content and add: Space for video; radio spots (see Silver Cedar Tunes Logo below for those); Quick Inquiry; Friendora link; 5 star rating on Rivo; a map; reviews from former patients. I am open to suggestions.

Target Market(s)

Those seeking individual and marital counseling.

Industry/Entity Type

Mental Health

Number of Pages Required

1 page

Font styles to use
Sans Serif
Other font styles liked:
• I'm open but no hard to read script

Requirements
Must have
• All the content on my home page with link for video and radio spots. List services and degrees and expertices (pics not necessary).
Nice to have
• A video of me and radio conversations (logo of Silver Cedar Tunes radio attached).
Should not have
• Cartoons, comedy, etc.... I don't need pictures of services (marital, depression, etc...) Just list those.

```html
<!DOCTYPE html>
<html lang="en">
<head>
<meta charset="utf-8">
<title>Dr. Mara K. Kalvoric — Individual and Marital Counseling</title>
<link href="https://fonts.googleapis.com/css2?family=Dancing+Script:wght@700&family=Lato:ital,wght@0,400;0,700;0,900;1,700;1,900&display=swap" rel="stylesheet">
<style>
:root{
  --blue:#2f84c2;
  --blue-dark:#2874ad;
  --orange:#f58220;
  --ink:#333;
  --muted:#555;
  --line:#d6d6d6;
  --white:#fff;
  --script:"Dancing Script",cursive;
  --sans:"Lato",Arial,sans-serif;
}
*{box-sizing:border-box;margin:0;padding:0}
html,body{width:1200px;height:2169px;overflow:hidden;background:var(--white)}
body{position:relative;font-family:var(--sans);color:var(--ink)}
.abs{position:absolute}
a{color:inherit;text-decoration:none}

/* top bar */
.topbar{left:0;top:0;width:1200px;height:36px;background:var(--blue)}
.social{left:80px;top:9px;display:flex;gap:10px;font-size:12px;color:var(--white);font-weight:700}
.social span{border:1px solid rgba(255,255,255,.8);border-radius:10px;padding:1px 8px}
.appt{left:908px;top:0;width:212px;height:36px;background:var(--orange);color:var(--white);font-size:16px;font-weight:700;display:flex;align-items:center;justify-content:center;gap:8px}

/* header */
.brand{left:80px;top:50px;font-family:var(--script);font-size:40px;color:var(--orange)}
.contact-top{right:80px;top:64px;display:flex;gap:26px;font-size:16px;color:var(--ink);font-weight:700}
.contact-top span{display:flex;align-items:center;gap:8px}

/* nav */
.nav{left:0;top:118px;width:1200px;height:48px;background:var(--blue)}
.nav ul{list-style:none;display:flex;position:absolute;left:80px;top:0;width:1040px;height:48px}
.nav li{flex:1;display:flex;align-items:center;justify-content:center;color:var(--white);font-weight:700;font-size:16px;position:relative}
.nav li+li::before{content:"";position:absolute;left:0;top:17px;height:14px;border-left:1px solid rgba(255,255,255,.35)}
.nav li.active{background:var(--orange)}

/* hero */
.hero{left:0;top:166px;width:1200px;height:521px;background:linear-gradient(100deg,#6b5a4e 0%,#c9c2b7 30%,#e6e2da 60%,#f0eeea 100%)}
.hero-caption{left:80px;top:463px;width:354px;height:130px;background:rgba(40,40,40,.82);color:var(--white);padding:18px 22px}
.hero-caption h1{font-style:italic;font-weight:900;font-size:28px;line-height:1.3}
.dots{display:flex;gap:8px;margin-top:14px}
.dots i{width:11px;height:11px;border-radius:50%;background:#ddd}
.dots i.on{background:none;border:2px solid var(--orange)}
.hero-curve{left:0;top:560px}

/* about */
.about-title{left:80px;top:706px;font-family:var(--script);font-size:42px;color:var(--orange)}
.rule{height:1px;background:var(--line)}
.rule::before{content:"";display:block;width:132px;height:3px;background:var(--blue);margin-top:-1px}
.about-text{left:80px;top:774px;width:648px;font-size:13.4px;line-height:22.6px;color:var(--ink)}
.btn{display:inline-block;color:var(--white);font-weight:900;font-size:12.5px;padding:7px 12px;letter-spacing:.3px}
.btn.orange{background:var(--orange)}
.btn.blue{background:var(--blue)}
.video{left:763px;top:716px;width:357px;height:238px;background:linear-gradient(120deg,#dfe3e6,#8e959b 60%,#3d4248);}
.video-bar{left:763px;top:920px;width:357px;height:34px;background:#2c2f33}

/* expertise */
.expertise{left:0;top:1016px;width:1200px;height:507px;background:linear-gradient(90deg,#2c2c2c 0%,#4a4a4a 50%,#3a3a3a 100%)}
.exp-title{left:0;top:1040px;width:1200px;text-align:center;font-family:var(--script);font-size:40px;color:var(--white)}
.exp-rule{left:340px;top:1104px;width:520px;height:1px;background:rgba(255,255,255,.35)}
.exp-rule::after{content:"";position:absolute;left:192px;top:-1px;width:136px;height:3px;background:var(--orange)}
.tabs{left:80px;top:1141px;width:238px;height:343px;background:var(--white);border-left:6px solid #ccc}
.tab{height:68.6px;display:flex;align-items:center;padding-left:20px;font-size:17px;font-weight:700;color:var(--ink);border-bottom:1px solid #bbb;line-height:1.25}
.tab.active{background:var(--orange);color:var(--white);margin-left:-6px;padding-left:26px}
.panel{left:318px;top:1141px;width:742px;height:343px;background:var(--white);border-left:1px solid var(--orange);padding:20px 20px 0 20px}
.panel h3{font-family:var(--script);font-size:28px;color:var(--orange);font-weight:700}
.panel p{width:530px;font-size:13.6px;line-height:21.5px;margin-top:12px}
.panel ul{list-style:none;margin-top:10px;font-size:13.2px}
.panel li{line-height:28px;padding-left:16px;position:relative}
.panel li::before{content:"›";position:absolute;left:0;top:-1px;font-weight:900;font-size:17px}
.portrait{left:882px;top:1178px;width:318px;height:345px;background:radial-gradient(circle at 50% 35%,#e8c79a 0%,#d7b27e 30%,#3f6e9c 70%,#2e5a85 100%);border-radius:160px 160px 0 0}

/* lower columns */
.col-title{font-family:var(--script);font-size:32px;color:var(--orange);top:1574px}
.col-rule{top:1630px}
.sessions{left:80px;top:1650px;width:340px;display:grid;grid-template-columns:143px 1fr;row-gap:14px;font-size:13px}
.sessions span::before{content:"✔";color:var(--orange);margin-right:6px}
.form{left:487px;top:1656px;width:261px}
.form div{border:1px solid #999;height:30px;font-size:13px;padding:7px 9px;margin-bottom:10px}
.form div.msg{height:52px}
.quote{left:796px;top:1660px;width:324px;height:114px;border:1px solid #ccc;border-radius:12px;padding:16px 24px 0 60px;font-style:italic;font-size:13px;line-height:19px}
.quote .q{position:absolute;font-size:46px;color:#ccc;font-family:Georgia,serif;font-style:normal;line-height:1}
.arrows{left:1084px;top:1588px;font-size:20px;font-weight:900;letter-spacing:10px}

/* footer */
.footer{left:0;top:1894px;width:1200px;height:231px;background:var(--blue);color:var(--white)}
.fnav{left:0;top:1920px;width:1200px;display:flex;justify-content:center;gap:0;font-size:13.5px;font-weight:700;color:var(--white)}
.fnav span{padding:0 24px;position:relative}
.fnav span+span::before{content:"|";position:absolute;left:-2px;opacity:.6}
.fnav .active{color:var(--orange)}
.fline{left:180px;width:840px;height:1px;background:rgba(255,255,255,.3)}
.fcontact{left:0;top:1982px;width:1200px;display:flex;justify-content:center;gap:24px;font-size:16px;align-items:center}
.fcontact span{display:flex;align-items:center;gap:12px}
.ficon{width:30px;height:30px;border-radius:50%;background:var(--blue-dark);display:flex;align-items:center;justify-content:center}
.donate{left:0;top:2054px;width:1200px;display:flex;justify-content:center;align-items:center;gap:20px;font-size:14.5px;font-weight:700}
.badge{width:102px;height:46px;background:var(--white)}
.copy{left:0;top:2125px;width:1200px;height:44px;background:var(--orange);color:var(--white);font-size:12px;font-weight:700;display:flex;align-items:center;justify-content:center}
</style>
</head>
<body>

<header>
  <div class="abs topbar"></div>
  <div class="abs social"><span>Friendora</span><span>Chirpline</span></div>
  <a class="abs appt" href="#">
    <svg width="18" height="18" viewBox="0 0 18 18"><circle cx="9" cy="9" r="7.5" fill="none" stroke="#fff" stroke-width="2"/><path d="M9 4v5h4" fill="none" stroke="#fff" stroke-width="2"/></svg>
    Make An Appointment
  </a>
  <div class="abs brand">Dr. Mara K. Kalvoric</div>
  <div class="abs contact-top">
    <span><svg width="20" height="20" viewBox="0 0 20 20"><path d="M4 2l4 4-2 3c1 2 3 4 5 5l3-2 4 4-3 3C8 19 1 12 1 5z" fill="var(--blue)"/></svg>(949) 555 0142</span>
    <span><svg width="28" height="18" viewBox="0 0 28 18"><rect width="28" height="18" fill="var(--blue)"/><path d="M1 1l13 10L27 1" fill="none" stroke="#fff" stroke-width="2"/></svg>mk@drkalvoric.com</span>
  </div>
  <nav class="abs nav">
    <ul>
      <li class="active">HOME</li><li>BIO</li><li>MY EXPERTISE</li><li>RESOURCES</li><li>SESSIONS</li><li>CONTACT ME</li>
    </ul>
  </nav>
</header>

<section>
  <div class="abs hero" role="img" aria-label="Photo of a man talking with a counselor on a couch"></div>
  <div class="abs hero-caption">
    <h1>I Provide Individual And Marital Counseling.</h1>
    <div class="dots"><i></i><i class="on"></i><i></i><i></i></div>
  </div>
  <svg class="abs hero-curve" width="1200" height="130" viewBox="0 0 1200 130">
    <path d="M0 127 Q420 40 1200 38 L1200 60 Q480 62 0 130 Z" fill="var(--orange)"/>
    <path d="M0 130 Q480 62 1200 60 L1200 130 Z" fill="#fff"/>
  </svg>
</section>

<section>
  <h2 class="abs about-title">About Dr. Mara K. Kalvoric</h2>
  <div class="abs rule" style="left:80px;top:760px;width:648px"></div>
  <div class="abs about-text">
    <p>I'm so glad you are here.&nbsp; Choosing to see a professional for issues in your life can be difficult but also possibly life changing.&nbsp; Many postpone seeking help because they believe doing so acknowledges failure on their part.&nbsp; Reallly? We seek the help of experts all the time (contractors, mechanics, chefs, etc...) and what is more important than your life? Consulting with a neutral party to act in your best interest can be time well spent.&nbsp; So if you are willing to take the time to invest in counseling, make sure that it is with someone that is worth your time.</p>
    <a class="btn orange" href="#" style="margin-top:16px">READ MORE</a>
  </div>
  <div class="abs video" role="img" aria-label="Video still of a counseling session"></div>
  <svg class="abs" style="left:910px;top:796px" width="64" height="64" viewBox="0 0 64 64"><circle cx="32" cy="32" r="30" fill="rgba(0,0,0,.55)"/><path d="M25 19l20 13-20 13z" fill="#fff"/></svg>
  <div class="abs video-bar"></div>
  <svg class="abs" style="left:775px;top:928px" width="250" height="18" viewBox="0 0 250 18"><path d="M2 3l11 6-11 6z" fill="#fff"/><path d="M28 6h4l5-4v14l-5-4h-4z" fill="#fff"/><rect x="60" y="7" width="190" height="5" rx="2" fill="#555"/><rect x="60" y="7" width="90" height="5" rx="2" fill="var(--blue)"/></svg>
</section>

<section>
  <div class="abs expertise" role="img" aria-label="Dim background photo of a counseling conversation"></div>
  <h2 class="abs exp-title">My Expertise</h2>
  <div class="abs exp-rule"></div>
  <div class="abs tabs">
    <div class="tab">Dating / Marriage</div>
    <div class="tab active">Parenting &amp; Professional Relationships</div>
    <div class="tab">Depression &amp; Anxiety Issues</div>
    <div class="tab">Personality Disorders</div>
    <div class="tab" style="border-bottom:0">Life Management</div>
  </div>
  <div class="abs panel">
    <h3>Parenting &amp; Professional Relationships</h3>
    <p>Lorem ipsum dolor sit amet, consectetuer adipiscing elit, sed diam nonummy nibh euismod tincidunt ut laoreetfgf dolore magna aliquam erat volutpat. tincidunt ut laoreetfgf dolore magna aliquam erat volutpat. Lorem ipsum dolor sit amet, consectetuer adipiscing elit, sed diam nonummy nibh euismod tincidunt.</p>
    <ul>
      <li>Lorem ipsum dolor sit amet consectetuer.</li>
      <li>Adipiscing elit&nbsp; sed diam nonummy nibh</li>
      <li>Laoreetfgf dolore magna aliquam erat volutpat</li>
      <li>Sed diam nonummy nibh euismod tincidunt</li>
    </ul>
    <a class="btn blue" href="#" style="margin-top:12px">READ MORE</a>
  </div>
  <div class="abs portrait" role="img" aria-label="Portrait photo of the psychologist"></div>
</section>

<section>
  <h2 class="abs col-title" style="left:80px">My Sessions</h2>
  <div class="abs rule col-rule" style="left:80px;width:332px"></div>
  <div class="abs sessions">
    <span>Individual Sessions</span><span>Divorce Mediation</span>
    <span>Marriage Sessions</span><span>Custody Evaluation Sessions</span>
    <span>Family Sessions</span><span>Testing Sessions</span>
    <span>Phone Sessions</span><span>Weekend / Holiday Sessions</span>
  </div>
  <a class="abs btn blue" href="#" style="left:80px;top:1802px">READ MORE</a>

  <h2 class="abs col-title" style="left:487px">Quick Inquiry</h2>
  <div class="abs rule col-rule" style="left:487px;width:261px"></div>
  <div class="abs form">
    <div>Name</div><div>Email</div><div class="msg">Message</div>
    <a class="btn blue" href="#" style="padding:7px 28px;margin-top:0">SEND</a>
  </div>

  <h2 class="abs col-title" style="left:789px">Radio Conversations</h2>
  <div class="abs arrows">‹ ›</div>
  <div class="abs rule col-rule" style="left:789px;width:331px"></div>
  <div class="abs quote">
    <span class="q" style="left:16px;top:8px">“</span>
    Lorem ipsum dolor sit amet, consectetuer adipiscing elit, sed diam nonummy nibh euismod tincidunt ut laoreetfgf dolore magna aliquam erat volutpat. tincidunt ut laoreetfgf.
    <span class="q" style="right:14px;bottom:-12px">”</span>
  </div>
  <div class="abs" style="left:1002px;top:1798px;font-size:12.5px;line-height:18px">
    <div style="color:var(--orange);font-weight:700">- Lorem ipsum dolor</div>
    <div style="color:var(--blue);padding-left:6px">Sitamet, CA</div>
  </div>
</section>

<footer>
  <div class="abs footer"></div>
  <div class="abs fnav"><span class="active">HOME</span><span>BIO</span><span>MY EXPERTISE</span><span>RESOURCES</span><span>SESSIONS</span><span>CONTACT ME</span></div>
  <div class="abs fline" style="top:1962px"></div>
  <div class="abs fcontact">
    <span><i class="ficon"><svg width="12" height="16" viewBox="0 0 12 16"><path d="M6 0a6 6 0 0 1 6 6c0 4-6 10-6 10S0 10 0 6a6 6 0 0 1 6-6z" fill="#fff"/><circle cx="6" cy="6" r="2" fill="var(--blue-dark)"/></svg></i>412 Harbor Lane, Suite 210 Seaview, CA 92600</span>
    <span><i class="ficon"><svg width="14" height="14" viewBox="0 0 20 20"><path d="M4 2l4 4-2 3c1 2 3 4 5 5l3-2 4 4-3 3C8 19 1 12 1 5z" fill="#fff"/></svg></i>(949) 555 0142</span>
    <span><i class="ficon"><svg width="14" height="10" viewBox="0 0 28 18"><rect width="28" height="18" fill="#fff"/><path d="M1 1l13 10L27 1" fill="none" stroke="var(--blue-dark)" stroke-width="2"/></svg></i>mk@drkalvoric.com</span>
  </div>
  <div class="abs fline" style="top:2032px"></div>
  <div class="abs donate">A portion of all revenue is donated to <div class="badge"></div><div class="badge"></div></div>
  <div class="abs copy">Copyright © 2016 Dr. Mara K. Kalvoric. All Rights Reserved.</div>
</footer>

</body>
</html>
```